Animation College website

Name of College: Brightloom Academy of 3D Animation and VFX

We need a redesigned modern website for Brightloom. The web-design should communicate a VFX and animation school and education. We will also need full access to the website once completed. We will also need access to the website to be able to make changes to the content and site ideally the website would be built on Wordpress.

To learn more about what the College please visit: http://brightloom-academy.example/
The video on the homepage demonstrates why Brightloom is a unique college offering 3D animation and VFX. The direct link to the video can be watched here: https://videohost.example/482915036

Client Profile Summary: Brightloom is an improved concept in job skills training for the 3D animation and visual effects industries. Our high graduate job placement numbers are based on the assertion that job skills must include more than simply learning to use software tools. Where nearly every digital media program teaches tools, job skills training should be about learning how to do a job in addition to learning how to use software tools. Brightloom is taught in an apprenticeship style with very experienced faculty mentoring and teaching students to learn how to master their craft (VFX and animation) so they can seamlessly step into industry and excel.

Target Market(s)

High school students, students interested in learning about animation and 3D.

Industry/Entity Type

College

Coding

Coded - Design and coding required

Number of Pages Required

5+ page

Font styles to use
Sans Serif

Colors

Designer to choose colors to be used in the design.

Requirements
Must have
• Please include the video on the current Brightloom-academy.example website. https://videohost.example/482915036
• Use the same content on the current brightloom-academy.example website.
• Include a page to showcase student work.
• Website must also be mobile responsive.
Should not have
• The attached PDF of the landing page is just an example of something we like. You do not have to replicate this. The PDF landing page is showing the colour blue you should incorporate.

```html
<!DOCTYPE html>
<html lang="en">
<head>
<meta charset="utf-8">
<title>Brightloom Academy of 3D Animation and VFX</title>
<link rel="stylesheet" href="https://fonts.googleapis.com/css2?family=Open+Sans:wght@300;400;600;700&display=swap">
<style>
:root{
  --blue:#1a6fa8;
  --blue-dark:#135a8a;
  --heading:#1f74b3;
  --text:#222;
  --muted:#8a8a8a;
  --panel:#2b2b2b;
  --footer:#262626;
  --white:#fff;
}
*{box-sizing:border-box;margin:0;padding:0}
html,body{width:1200px;height:2975px;overflow:hidden}
body{font-family:"Open Sans",Arial,sans-serif;color:var(--text);background:var(--white);position:relative}
.hero{position:absolute;left:0;top:0;width:1200px;height:615px;background:linear-gradient(135deg,#3a4a3e 0%,#1c2226 40%,#2c3a44 70%,#151a1e 100%)}
.brand{position:absolute;left:133px;top:22px;display:flex;align-items:center;gap:12px;color:var(--white)}
.brand-mark{width:40px;height:40px;background:var(--white)}
.brand-name{font-size:30px;font-weight:700;line-height:1}
.brand-sub{font-size:12px;font-weight:400;margin-top:4px}
.arrow{position:absolute;top:296px;width:14px;height:24px}
.arrow.left{left:24px}.arrow.right{right:24px}
.hero-caption{position:absolute;left:133px;top:512px;color:var(--white)}
.hero-caption h1{font-size:21px;font-weight:400}
.hero-caption p{font-size:17px;margin-top:6px}
.partners{position:absolute;left:0;top:615px;width:1200px;height:95px;background:var(--blue)}
.badge{position:absolute;top:622px;background:rgba(255,255,255,.9)}
.b1{left:133px;width:46px;height:60px;border-radius:4px}
.b2{left:233px;top:622px;width:78px;height:78px;border-radius:50%}
.b3{left:357px;width:78px;height:78px;border-radius:50%}
.b4{left:495px;top:626px;width:62px;height:64px;border-radius:4px}
.b5{left:628px;top:632px;width:82px;height:52px;border-radius:4px}
.form{position:absolute;left:763px;top:184px;width:304px;height:510px;background:var(--panel);padding:18px 24px;color:var(--white);text-align:center}
.form h2{font-size:27px;font-weight:400}
.form .lead{font-size:10.5px;line-height:1.35;margin:6px 0 14px}
.field{height:36px;background:var(--white);margin-bottom:12px;color:#555;font-size:10px;text-align:left;padding:10px 12px}
.field.tall{height:98px}
.submit{height:36px;background:var(--blue);font-size:15px;line-height:36px;margin-top:12px}
.section{position:absolute;left:133px;width:934px}
.section h2{font-size:25px;font-weight:400;color:var(--heading)}
.section .sub{font-size:13.5px;margin-top:8px}
.section .body{font-size:11.5px;line-height:1.7;color:var(--muted);margin-top:12px}
.intro{top:785px}
.video-band{position:absolute;left:0;top:1011px;width:1200px;height:318px;background:linear-gradient(120deg,#0d2a4a 0%,#1c5d8e 40%,#0f3559 70%,#0a1f36 100%)}
.video{position:absolute;left:361px;top:1035px;width:478px;height:266px;background:linear-gradient(135deg,#3a3028,#6a4a36 45,#2a2624);background:linear-gradient(135deg,#2f2822 0%,#6b4a36 45%,#25211f 100%)}
.video-bar{position:absolute;left:0;bottom:0;width:100%;height:22px;background:rgba(0,0,0,.75)}
.video-title{position:absolute;right:68px;top:68px;color:#ddd;font-size:20px;font-weight:300}
.video-tools{position:absolute;right:8px;top:6px}
.learn{top:1395px}
.feature{position:absolute;top:1576px;width:297px}
.feature .photo{height:175px}
.feature h3{font-size:15.5px;font-weight:600;color:var(--heading);margin-top:14px}
.feature p{font-size:11.5px;line-height:1.6;color:var(--muted);margin-top:6px}
.f1{left:133px}.f1 .photo{background:linear-gradient(135deg,#2a2a2a,#8a6a58 60%,#1a1a1a)}
.f2{left:452px}.f2 .photo{background:linear-gradient(135deg,#1e3a4a,#4a7a5a 50%,#1a2028)}
.f3{left:770px}.f3 .photo{background:linear-gradient(135deg,#1a1614,#c8b8a8 40%,#6a2a1e 90%)}
.testimonial-band{position:absolute;left:0;top:1920px;width:1200px;height:321px;background:linear-gradient(110deg,#6a2a2a 0%,#3a3a44 35%,#8a8070 60%,#2a3440 100%)}
.quote-card{position:absolute;left:361px;top:1993px;width:478px;height:208px;background:var(--white);padding:70px 30px 0}
.quote-card p{font-size:11.5px;line-height:1.65;color:var(--muted)}
.quote-card .name{font-size:13.5px;color:var(--heading);margin-top:10px}
.quote-card .role{font-size:11.5px;margin-top:2px}
.qmark{position:absolute;font-size:70px;font-weight:700;color:#dcdcdc;line-height:1}
.q-open{left:24px;top:8px}.q-close{right:24px;bottom:-22px}
.avatar{position:absolute;left:559px;top:1951px;width:80px;height:80px;border-radius:50%;background:linear-gradient(135deg,#6a5a4e,#c0a08a);border:3px solid var(--white)}
.advantages{top:2315px}
.advantages ul{list-style:none;margin-top:14px}
.advantages li{font-size:11.5px;color:var(--heading);line-height:24px}
.advantages li::before{content:"•";color:var(--text);margin-right:8px}
.cta{position:absolute;left:0;top:2717px;width:1200px;height:159px;background:var(--blue);color:var(--white);text-align:center;padding-top:46px}
.cta h2{font-size:25px;font-weight:400}
.cta p{font-size:15px;margin-top:10px}
.footer{position:absolute;left:0;top:2876px;width:1200px;height:99px;background:var(--footer)}
.footer p{position:absolute;left:133px;top:42px;font-size:11.5px;color:#bbb}
.social{position:absolute;left:944px;top:36px;display:flex;gap:8px}
.social span{width:26px;height:26px;border-radius:50%;background:var(--blue)}
</style>
</head>
<body>
<header class="hero" role="img" aria-label="Photo of a student working at 3D animation workstations"></header>
<div class="brand"><span class="brand-mark"></span><div><div class="brand-name">Brightloom</div><div class="brand-sub">Academy of 3D Animation &amp; VFX</div></div></div>
<svg class="arrow left" viewBox="0 0 14 24"><path d="M12 2 2 12l10 10" fill="none" stroke="#ccc" stroke-width="2"/></svg>
<svg class="arrow right" viewBox="0 0 14 24"><path d="M2 2l10 10L2 22" fill="none" stroke="#ccc" stroke-width="2"/></svg>
<div class="hero-caption"><h1>3D Animation &amp; VFX One-Year Intensive Training Program</h1><p>Train alongside passionate and experienced industry masters</p></div>

<div class="partners"></div>
<div class="badge b1"></div><div class="badge b2"></div><div class="badge b3"></div><div class="badge b4"></div><div class="badge b5"></div>

<form class="form">
  <h2>Want to know More?</h2>
  <p class="lead">Complete this form to receive more information<br>about program details &amp; more</p>
  <div class="field">First name*</div>
  <div class="field">Last name*</div>
  <div class="field">Phone*</div>
  <div class="field">Email*</div>
  <div class="field">Country of Residence*</div>
  <div class="field tall">Comments</div>
  <div class="submit">SEND ME FREE INFO</div>
</form>

<section class="section intro">
  <h2>One-Year Intensive Training Program</h2>
  <p class="sub">Phasellus id rhoncus velit, non cursus lectus. Nam elementum, massa et ultrices varius</p>
  <p class="body">Praesent molestie nunc elit, id feugiat mauris lobortis non. Phasellus in imperdiet urna. Nam dapibus erat sit amet faucibus commodo. Vestibulum condimentum, risus ultrices sodales varius, velit nibh dignissim risus, eu tristique massa orci non enim. Nullam elementum eget velit ut molestie. Ut interdum vitae libero at tempor. Suspendisse quis nisi eu ipsum dictum finibus in non leo. Fusce id diam id ex finibus feugiat. Vivamus commodo est interdum luctus euismod. Vivamus consequat sapien nec turpis maximus tempor. Fusce id nulla vitae purus egestas laoreet in vitae ligula.</p>
</section>

<div class="video-band" role="img" aria-label="Blue hexagon pattern background"></div>
<div class="video" role="img" aria-label="Video player showing a graduate speaking about the academy">
  <span class="video-title">Phenomenal</span>
  <svg class="video-tools" width="14" height="80" viewBox="0 0 14 80"><circle cx="7" cy="8" r="4" fill="#fff"/><circle cx="7" cy="30" r="4" fill="none" stroke="#fff" stroke-width="1.5"/><circle cx="7" cy="52" r="4" fill="none" stroke="#fff" stroke-width="1.5"/><path d="M2 76 12 68 8 78z" fill="#fff"/></svg>
  <div class="video-bar"><svg width="478" height="22"><path d="M8 6v10l8-5z" fill="#fff"/><rect x="26" y="10" width="380" height="3" fill="#555"/><rect x="26" y="10" width="20" height="3" fill="#fff"/></svg></div>
</div>

<section class="section learn">
  <h2>Learn Animation &amp; Visual Effects Production from the Experts</h2>
  <p class="sub">Phasellus id rhoncus velit, non cursus lectus. Nam elementum, massa et ultrices varius</p>
  <p class="body">Duis euismod eu ante quis rhoncus. Nullam sed eleifend leo, non scelerisque purus. In nibh orci, varius id lectus non, efficitur egestas lectus. Vestibulum nisi leo, hendrerit sit amet diam non, tristique elementum ipsum. Donec at eros eu nulla porta scelerisque. Aliquam bibendum sit amet est eget pretium.</p>
  <p class="body">Etiam leo tellus, tristique quis consequat id, dapibus in massa. Suspendisse porta dolor vitae commodo congue. Donec ullamcorper sodales purus</p>
</section>

<article class="feature f1"><div class="photo" role="img" aria-label="Graduates holding diplomas"></div><h3>CORE SKILLS</h3><p>Duis pretium leo elit, id malesuada urna maximus id. Etiam aliquam finibus nisi, vitae sagittis risus viverra id. Curabitur ac consequat orci.</p></article>
<article class="feature f2"><div class="photo" role="img" aria-label="Students at a multi-monitor workstation"></div><h3>TRANSITION INTO PRACTICE</h3><p>Duis pretium leo elit, id malesuada urna maximus id. Etiam aliquam finibus nisi, vitae sagittis risus viverra id. Curabitur ac consequat orci.</p></article>
<article class="feature f3"><div class="photo" role="img" aria-label="Students on a lit film set with a clapperboard"></div><h3>PRACTICAL TRAINING</h3><p>Duis pretium leo elit, id malesuada urna maximus id. Etiam aliquam finibus nisi, vitae sagittis risus viverra id. Curabitur ac consequat orci.</p></article>

<div class="testimonial-band" role="img" aria-label="Blurred bokeh lights background"></div>
<blockquote class="quote-card">
  <span class="qmark q-open">“</span>
  <p>Duis pretium leo elit, id malesuada urna maximus id. Etiam aliquam finibus nisi, vitae sagittis risus viverra id. Curabitur ac consequat orci. Nam neque mauris, porttitor nec quam ac, dictum cursus magna. Donec tincidunt tellus id tincidunt dictum. Nunc vel ex porttitor massa rutrum pretium.</p>
  <div class="name">Dana Morrow</div>
  <div class="role">Lighting Artist Graduate</div>
  <span class="qmark q-close">”</span>
</blockquote>
<div class="avatar" role="img" aria-label="Portrait of the graduate"></div>

<section class="section advantages">
  <h2>The Brightloom Advantages</h2>
  <p class="sub">Phasellus id rhoncus velit, non cursus lectus. Nam elementum, massa et ultrices varius</p>
  <p class="body">Duis euismod eu ante quis rhoncus. Nullam sed eleifend leo, non scelerisque purus. In nibh orci, varius id lectus non, efficitur egestas lectus. Vestibulum nisi leo, hendrerit sit amet diam non, tristique elementum ipsum. Donec at eros eu nulla porta scelerisque. Aliquam bibendum sit amet est eget pretium.</p>
  <p class="body">Etiam leo tellus, tristique quis consequat id, dapibus in massa. Suspendisse porta dolor vitae commodo congue. Donec ullamcorper sodales purus</p>
  <ul>
    <li>Etiam vestibulum enim at auctor ullamcorper</li>
    <li>Quisque rutrum volutpat lectus ac posuere</li>
    <li>Nulla gravida pretium elit et condimentum</li>
    <li>Nam vitae metus posuere</li>
    <li>Morbi condimentum, eros non posuere</li>
    <li>Fusce egestas</li>
    <li>And More</li>
  </ul>
</section>

<section class="cta"><h2>Want to learn more?</h2><p>FILL OUT THE FORM ABOVE TO RECEIVE INFORMATION ABOUT THE PROGRAM!</p></section>

<footer class="footer">
  <p>Copyright © 2017 Brightloom Academy of 3D Animation and VFX. All rights reserved.</p>
  <div class="social"><span></span><span></span><span></span><span></span></div>
</footer>
</body>
</html>
```